Multi-Line Insurance PPC Landing Page - Conversion optimized.

We have a PPC landing page used for the general population to get an insurance quote through an agent's site.

We'd like to improve the page for PPC traffic, make it more conversion friendly.

Site should be a single long page.

We will dynamically change the form and headlines on the page depending on what insurance "line" is being called. ie, Lift, Auto, Home, Business.

The enclosed AI file has all of the raw elements we need. We're looking to enhance the design and conversion ability.

Target Market(s)

General public needed insurance services.

Industry/Entity Type

Insurance Broker

Number of Pages Required

1 page

Font styles to use
Sans Serif

Requirements
Must have
• Form, agent picture, name, address.

```html
<!DOCTYPE html>
<html lang="en">
<head>
<meta charset="utf-8">
<title>Insurance Agent – Get an Instant Quote</title>
<link rel="stylesheet" href="https://fonts.googleapis.com/css2?family=Open+Sans:wght@400;600;700&display=swap">
<style>
:root{
  --blue:#1f5aa6;
  --blue-dark:#16457f;
  --ink:#333;
  --muted:#666;
  --band:#eeeeee;
  --line:#d6d6d6;
  --hex:#3a3a3a;
  --white:#fff;
}
*{box-sizing:border-box;margin:0;padding:0}
html,body{width:721px;height:1200px;overflow:hidden}
body{font-family:"Open Sans",Arial,sans-serif;color:var(--ink);background:var(--white);position:relative}
.section-title{font-variant:small-caps;font-weight:600;font-size:19px;color:var(--ink);text-align:center;letter-spacing:.5px}
.section-title .accent{color:var(--blue)}
.title-rule{width:60px;height:2px;background:var(--blue);margin:4px auto 0}
.btn{display:inline-block;background:var(--blue);color:var(--white);font-size:8px;font-weight:700;letter-spacing:.4px;text-transform:uppercase;padding:4px 12px}

/* header */
.site-header{height:56px;display:flex;align-items:center;justify-content:space-between;padding:0 78px 0 78px}
.logo{font-size:26px;font-weight:700;color:var(--blue);letter-spacing:.5px}
.header-cta{display:flex;align-items:center;gap:10px}
.header-cta .btn{font-size:9px;padding:6px 10px}
.header-phone{display:flex;align-items:center;gap:4px;font-size:13px;font-weight:700;color:var(--blue)}

/* hero */
.hero{height:245px;background:linear-gradient(180deg,#5d6268 0%,#7b8086 45%,#9a9ea2 75%,#6c7074 100%)}

/* quote panel */
.quote-panel{position:absolute;top:283px;left:72px;width:577px;height:225px;background:var(--white);border-top:4px solid var(--blue);box-shadow:0 2px 8px rgba(0,0,0,.25);display:flex}
.agent-card{width:210px;padding:14px 10px;text-align:center}
.agent-photo{width:92px;height:92px;margin:0 auto;background:linear-gradient(160deg,#c9c2b8,#7d7873);border:4px solid #e3e3e3}
.agent-name{font-variant:small-caps;font-weight:600;color:var(--blue);font-size:13px;margin-top:8px}
.agent-contact{font-size:8px;color:var(--muted);margin-top:3px;display:flex;align-items:center;justify-content:center;gap:4px}
.agent-bio{font-size:8px;color:var(--muted);margin-top:8px;line-height:1.4}
.quote-form{flex:1;padding:12px 18px 10px 10px}
.form-title{font-variant:small-caps;font-weight:600;font-size:16px;color:var(--ink);text-align:center}
.form-title .accent{color:var(--blue)}
.form-grid{display:grid;grid-template-columns:1fr 1fr;column-gap:14px;row-gap:5px;margin-top:8px}
.field label{display:block;font-size:7px;color:var(--muted);margin-bottom:2px}
.field .input{height:13px;border:1px solid var(--line)}
.field .split{display:flex;gap:4px}
.field .split .input{flex:1;font-size:6px;color:#999;padding-left:3px;line-height:11px}
.form-submit{text-align:center;margin-top:8px}
.form-submit .btn{padding:5px 26px}

/* about */
.about{position:absolute;top:520px;left:0;width:721px;height:168px;background:var(--band);padding:22px 60px 0}
.about p{font-size:8px;color:var(--muted);text-align:center;line-height:1.5;margin-top:10px}

/* products */
.products{position:absolute;top:700px;left:0;width:721px;padding:0 70px}
.product-grid{display:grid;grid-template-columns:repeat(4,1fr);column-gap:30px;margin-top:22px}
.product{text-align:center}
.product svg{display:block;margin:0 auto}
.product h3{font-variant:small-caps;font-weight:600;font-size:13px;color:var(--blue);margin-top:10px}
.product p{font-size:7.5px;color:var(--muted);line-height:1.45;margin-top:4px}
.product .btn{margin-top:8px}

/* testimonials */
.testimonials{position:absolute;top:960px;left:0;width:721px;height:178px;background:var(--band);padding-top:14px}
.testimonial-row{position:relative;height:150px}
.t-photo{position:absolute;background:linear-gradient(160deg,#cdb9a8,#8a7565)}
.t-side-left{left:100px;top:8px;width:78px;height:88px}
.t-side-right{left:543px;top:8px;width:78px;height:88px}
.t-center{left:325px;top:0;width:72px;height:80px}
.t-arrow{position:absolute;top:40px}
.t-name{position:absolute;top:86px;width:100%;text-align:center;font-variant:small-caps;font-weight:600;font-size:11px;color:var(--blue)}
.t-quote{position:absolute;top:102px;left:230px;width:261px;text-align:center;font-size:7.5px;color:var(--muted);line-height:1.45}

/* footer */
.site-footer{position:absolute;top:1138px;left:0;width:721px;height:62px;background:var(--blue);color:var(--white);text-align:center;padding:7px 50px 0}
.site-footer h4{font-size:8px;font-weight:700}
.site-footer p{font-size:6.5px;line-height:1.4;opacity:.9}
.site-footer .copyright{margin-top:5px}
</style>
</head>
<body>

<header class="site-header">
  <div class="logo">Insurance Agent</div>
  <div class="header-cta">
    <span class="btn">Get a Quote</span>
    <span class="header-phone">
      <svg width="13" height="13" viewBox="0 0 24 24"><path fill="#1f5aa6" d="M6.6 10.8a15.1 15.1 0 0 0 6.6 6.6l2.2-2.2c.3-.3.7-.4 1-.2 1.1.4 2.3.6 3.6.6.6 0 1 .4 1 1V20c0 .6-.4 1-1 1C10.6 21 3 13.4 3 4c0-.6.4-1 1-1h3.5c.6 0 1 .4 1 1 0 1.3.2 2.5.6 3.6.1.3 0 .7-.2 1z"/></svg>
      123 555 0147
    </span>
  </div>
</header>

<div class="hero" role="img" aria-label="Businessman holding an umbrella under a stormy sky with lightning"></div>

<section class="quote-panel">
  <div class="agent-card">
    <div class="agent-photo" role="img" aria-label="Portrait photo of the insurance agent"></div>
    <div class="agent-name">Get An Instant</div>
    <div class="agent-contact">
      <svg width="8" height="8" viewBox="0 0 24 24"><path fill="#1f5aa6" d="M6.6 10.8a15.1 15.1 0 0 0 6.6 6.6l2.2-2.2c.3-.3.7-.4 1-.2 1.1.4 2.3.6 3.6.6.6 0 1 .4 1 1V20c0 .6-.4 1-1 1C10.6 21 3 13.4 3 4c0-.6.4-1 1-1h3.5c.6 0 1 .4 1 1 0 1.3.2 2.5.6 3.6.1.3 0 .7-.2 1z"/></svg>
      123 555 0147
    </div>
    <div class="agent-contact">
      <svg width="8" height="8" viewBox="0 0 24 24"><path fill="#1f5aa6" d="M3 5h18v14H3zm2 2v.5l7 4.5 7-4.5V7z"/></svg>
      info@harborline-agency.com
    </div>
    <p class="agent-bio">Lorem ipsum dolor sit amet, conse<br>ctetur adipiscing elit, sed diam nonummy<br>nibh euismod tincidunt</p>
  </div>
  <div class="quote-form">
    <h2 class="form-title"><span class="accent">Get An Instant</span> Insurance Quote.</h2>
    <div class="form-grid">
      <div class="field"><label>Full Name</label><div class="input"></div></div>
      <div class="field"><label>Type of Insurance</label><div class="input"></div></div>
      <div class="field"><label>City</label><div class="input"></div></div>
      <div class="field"><label>Telephone No.</label><div class="input"></div></div>
      <div class="field"><label>State</label><div class="input"></div></div>
      <div class="field"><label>Zip Code</label><div class="input"></div></div>
      <div class="field"><label>Date of Birth</label><div class="split"><div class="input">Month</div><div class="input">Day</div><div class="input">Year</div></div></div>
      <div class="field"><label>Address</label><div class="input"></div></div>
      <div class="field"><label>Current Insurer</label><div class="input"></div></div>
      <div class="field"><label>Email</label><div class="input"></div></div>
    </div>
    <div class="form-submit"><span class="btn">Submit</span></div>
  </div>
</section>

<section class="about">
  <h2 class="section-title"><span class="accent">About</span> Insurance Agent</h2>
  <div class="title-rule"></div>
  <p>Lorem ipsum dolor sit amet, consectetur adipiscing elit, sed diam nonummy nibh euismod tincidunt ut laoreet dolore magna aliquam erat volutpat. Ut wisi enim ad minim veniam, quis nostrud exerci tation ullamcorper suscipit lobortis nisl ut aliquip ex ea commodo consequat. Duis autem vel eum iriure dolor in hendrerit in vulputate velit esse molestie consequat, vel illum dolore eu feugiat nulla facilisis at vero eros et accumsan et iusto odio dignissim qui blandit praesent luptatum zzril delenit augue duis dolore te feugait nulla facilisi.</p>
</section>

<section class="products">
  <h2 class="section-title"><span class="accent">Our</span> Insurance Products</h2>
  <div class="title-rule"></div>
  <div class="product-grid">
    <div class="product">
      <svg width="80" height="88" viewBox="0 0 80 88"><polygon points="40,2 78,23 78,65 40,86 2,65 2,23" fill="#3a3a3a"/><path d="M22 46a18 18 0 0 1 36 0z" fill="#fff"/><path d="M40 46v16a4 4 0 0 1-8 0" stroke="#fff" stroke-width="3" fill="none"/></svg>
      <h3>Life</h3>
      <p>Lorem ipsum dolor sit amet, consectetuer adipiscing elit, sed diam nonummy nibh euismod tincidunt.</p>
      <span class="btn">Get a Quote</span>
    </div>
    <div class="product">
      <svg width="80" height="88" viewBox="0 0 80 88"><polygon points="40,2 78,23 78,65 40,86 2,65 2,23" fill="#3a3a3a"/><path d="M20 52v-8l5-10h30l5 10v8z" fill="#fff"/><rect x="28" y="37" width="24" height="7" fill="#3a3a3a"/><circle cx="28" cy="54" r="4" fill="#fff" stroke="#3a3a3a" stroke-width="2"/><circle cx="52" cy="54" r="4" fill="#fff" stroke="#3a3a3a" stroke-width="2"/></svg>
      <h3>Auto</h3>
      <p>Lorem ipsum dolor sit amet, consectetuer adipiscing elit, sed diam nonummy nibh euismod tincidunt.</p>
      <span class="btn">Get a Quote</span>
    </div>
    <div class="product">
      <svg width="80" height="88" viewBox="0 0 80 88"><polygon points="40,2 78,23 78,65 40,86 2,65 2,23" fill="#3a3a3a"/><path d="M40 24 18 44h6v18h12V50h8v12h12V44h6z" fill="#fff"/></svg>
      <h3>Home</h3>
      <p>Lorem ipsum dolor sit amet, consectetuer adipiscing elit, sed diam nonummy nibh euismod tincidunt.</p>
      <span class="btn">Get a Quote</span>
    </div>
    <div class="product">
      <svg width="80" height="88" viewBox="0 0 80 88"><polygon points="40,2 78,23 78,65 40,86 2,65 2,23" fill="#3a3a3a"/><rect x="20" y="34" width="40" height="26" rx="2" fill="#fff"/><path d="M33 34v-5h14v5" stroke="#fff" stroke-width="3" fill="none"/><rect x="20" y="44" width="40" height="2" fill="#3a3a3a"/></svg>
      <h3>Business</h3>
      <p>Lorem ipsum dolor sit amet, consectetuer adipiscing elit, sed diam nonummy nibh euismod tincidunt.</p>
      <span class="btn">Get a Quote</span>
    </div>
  </div>
</section>

<section class="testimonials">
  <h2 class="section-title"><span class="accent">Client</span> Testimonials</h2>
  <div class="title-rule"></div>
  <div class="testimonial-row">
    <svg class="t-arrow" style="left:58px" width="14" height="24" viewBox="0 0 14 24"><path d="M12 2 2 12l10 10" stroke="#999" stroke-width="2" fill="none"/></svg>
    <div class="t-photo t-side-left" style="clip-path:polygon(50% 0,100% 25%,100% 75%,50% 100%,0 75%,0 25%)" role="img" aria-label="Photo of a client"></div>
    <div class="t-photo t-center" style="clip-path:polygon(50% 0,100% 25%,100% 75%,50% 100%,0 75%,0 25%);border:3px solid #fff" role="img" aria-label="Photo of the featured client"></div>
    <div class="t-photo t-side-right" style="clip-path:polygon(50% 0,100% 25%,100% 75%,50% 100%,0 75%,0 25%)" role="img" aria-label="Photo of a client"></div>
    <svg class="t-arrow" style="left:650px" width="14" height="24" viewBox="0 0 14 24"><path d="M2 2l10 10L2 22" stroke="#999" stroke-width="2" fill="none"/></svg>
    <div class="t-name">Lorem Ipsum Dolor Sit</div>
    <p class="t-quote">Lorem ipsum dolor sit amet, consectetuer adipiscing elit, sed diam nonummy nibh euismod tincidunt ut laoreet dolore.</p>
  </div>
</section>

<footer class="site-footer">
  <h4>Disclaimer :</h4>
  <p>Lorem ipsum dolor sit amet, consectetur adipiscing elit, sed diam nonummy nibh euismod tincidunt ut laoreet dolore magna aliquam erat volutpat. Ut wisi enim ad minim veniam, quis nostrud exerci tation ullamcorper suscipit lobortis nisl ut aliquip ex ea commodo consequat.</p>
  <p class="copyright">Copyright © 2015 Insurance Agent &nbsp;|&nbsp; All rights reserved</p>
</footer>

</body>
</html>
```